Quiet Lanterns for the Restless Inner Mind

I would like a website designed that would be used to upload podcasts, videos and written material about mental health. Where people will be being as honest, open and truthful as they can about mental health issues.
I would like it to look calming and soothing. Inspired by Dorlac's paintings and colour schemes.

I am on Brightlane as Dr Helen Maddox - and chirpbox as drhelenmaddox

Target Market(s)

Healthcare professionals and users of services who want to think at a deeper level about the nature of mental illness

Number of Pages Required

1 page

```html
<!DOCTYPE html>
<html lang="en">
<head>
<meta charset="utf-8">
<title>Dr Helen Maddox</title>
<link rel="stylesheet" href="https://fonts.googleapis.com/css2?family=Bebas+Neue&family=Open+Sans:wght@400;600&display=swap">
<style>
:root{
  --ink:#222222;
  --text:#3a3a3a;
  --dark:#242424;
  --green:#c8f59c;
  --green-strong:#9ddc5a;
  --green-soft:#eefbe2;
  --salmon:#f4896b;
  --salmon-soft:#f7b29a;
  --white:#ffffff;
  --line:#dcdcdc;
}
*{box-sizing:border-box;margin:0;padding:0}
html,body{width:1200px;height:3673px;overflow:hidden}
body{position:relative;background:var(--white);font-family:"Open Sans",Arial,sans-serif;color:var(--text)}
.display{font-family:"Bebas Neue",Impact,sans-serif;font-weight:400;letter-spacing:.5px}
.abs{position:absolute}

/* header */
.site-header{position:absolute;left:0;top:0;width:1200px;height:86px;background:var(--dark)}
.brand{position:absolute;left:113px;top:26px;font-size:30px;color:var(--white)}
.menu-btn{position:absolute;left:1050px;top:24px;width:38px;height:38px}

/* hero */
.hero{position:absolute;left:0;top:86px;width:1200px;height:514px;
  background:radial-gradient(ellipse at 30% 30%,#e0a25a 0%,#a8622e 35%,#5a3220 75%,#3a2418 100%)}
.hero-kicker{position:absolute;width:100%;top:288px;text-align:center;font-size:32px;color:var(--white)}
.hero-title{position:absolute;width:100%;top:320px;text-align:center;font-size:62px;color:var(--white)}
.hero-arrow{position:absolute;left:574px;top:411px;width:52px;height:52px}

/* section titles */
.section-title{position:absolute;left:0;width:1200px;height:70px;display:flex;align-items:center}
.stripes{flex:1;position:relative;height:40px}
.stripes span{position:absolute;height:12px}
.stripes.left span{background:var(--green);left:0;clip-path:polygon(0 0,100% 0,calc(100% - 12px) 100%,0 100%)}
.stripes.left span:first-child{top:7px;right:0}
.stripes.left span:last-child{top:32px;right:18px}
.stripes.right span{background:var(--salmon-soft);right:0;clip-path:polygon(12px 0,100% 0,100% 100%,0 100%)}
.stripes.right span:first-child{top:7px;left:18px}
.stripes.right span:last-child{top:32px;left:0}
.section-title h2{font-family:"Bebas Neue",Impact,sans-serif;font-weight:400;font-size:62px;color:var(--ink);padding:0 12px;line-height:1}
.intro{position:absolute;left:0;width:1200px;text-align:center;font-size:15.5px;line-height:28px;color:var(--text)}

.btn{position:absolute;width:163px;height:42px;background:var(--salmon);color:var(--white);font-size:14.5px;text-align:center;line-height:42px;letter-spacing:.3px}

/* video cards */
.video{position:absolute;top:899px;width:311px}
.video .thumb{height:218px;position:relative}
.video .play{position:absolute;left:140px;top:93px}
.video p{text-align:center;font-size:21px;margin-top:20px;color:var(--ink)}

/* conversation cards */
.talk{position:absolute;width:461px;height:102px;border:1px solid var(--line);background:var(--white)}
.talk .thumb{position:absolute;left:0;top:0;width:100px;height:100px}
.talk h3{position:absolute;left:122px;top:16px;font-size:17.5px;font-weight:400;color:var(--ink)}
.talk p{position:absolute;left:122px;top:48px;width:250px;font-size:11.5px;line-height:18px;color:var(--text)}
.talk svg{position:absolute;left:410px;top:38px}

/* about */
.about-frame{position:absolute;left:95px;top:2220px;width:260px;height:320px;background:var(--green-soft)}
.about-photo{position:absolute;left:111px;top:2116px;width:348px;height:408px;background:linear-gradient(120deg,#d8d4cf 0%,#b8a18c 45%,#eeeae4 100%)}
.about-copy{position:absolute;left:536px;top:2163px;width:556px;font-size:15.5px;line-height:28.5px}
.about-copy p+p{margin-top:17px}

/* articles */
.article{position:absolute;top:2830px;width:463px;height:432px;background:var(--white);box-shadow:0 2px 14px rgba(0,0,0,.12)}
.article .thumb{height:211px}
.article h3{position:absolute;left:24px;top:244px;font-size:19.5px;font-weight:400;color:var(--ink)}
.article .date{position:absolute;left:24px;top:284px;font-size:15px;color:var(--salmon)}
.article p{position:absolute;left:24px;top:319px;width:415px;font-size:15px;line-height:26px;text-align:justify}

/* footer */
.site-footer{position:absolute;left:0;top:3408px;width:1200px;height:265px;background:var(--dark);color:var(--white)}
.site-footer .f-brand{position:absolute;left:110px;top:42px;font-size:30px}
.site-footer .f-about{position:absolute;left:111px;top:82px;width:290px;font-size:14px;line-height:24px}
.f-head{position:absolute;top:42px;font-size:20px;padding-bottom:8px;border-bottom:2px solid var(--green-strong)}
.f-item{position:absolute;font-size:15px;line-height:25px;padding-left:32px}
.f-item svg{position:absolute;left:0;top:5px}
.social{position:absolute;left:990px;font-size:14px;line-height:30px;padding-left:40px}
.social::before{content:"";position:absolute;left:0;top:0;width:30px;height:30px;border:1.5px solid var(--white);border-radius:50%}
.copyright{position:absolute;left:0;width:100%;top:222px;text-align:center;font-size:15px}
</style>
</head>
<body>

<header class="site-header">
  <div class="brand display">Dr Helen Maddox</div>
  <svg class="menu-btn" viewBox="0 0 38 38" aria-label="Menu">
    <circle cx="19" cy="19" r="17.5" fill="none" stroke="#fff" stroke-width="1.5"/>
    <path d="M12 13h14M12 19h14M12 25h14" stroke="#fff" stroke-width="1.5"/>
  </svg>
</header>

<section class="hero">
  <div role="img" aria-label="Two young people laughing together outdoors in warm evening light" style="position:absolute;inset:0"></div>
  <div class="hero-kicker display">Welcome to</div>
  <h1 class="hero-title display">Dr Helen Maddox</h1>
  <svg class="hero-arrow" viewBox="0 0 52 52" aria-label="Scroll down">
    <circle cx="26" cy="26" r="24.5" fill="none" stroke="#fff" stroke-width="2"/>
    <path d="M26 14v24M18 30l8 8 8-8" fill="none" stroke="#fff" stroke-width="2"/>
  </svg>
</section>

<!-- videos -->
<div class="section-title" style="top:676px">
  <div class="stripes left"><span></span><span></span></div>
  <h2>Mental Health Video</h2>
  <div class="stripes right"><span></span><span></span></div>
</div>
<p class="intro" style="top:788px">Lorem ipsum dolor sit amet, consectetur adipiscing elit, sed do eiusmod tempor incididunt ut labore et dolore magna aliqua.<br>Quis ipsum suspendisse ultrices gravida. Risus commodo viverra maecenas accumsan lacus vel facilisis.</p>

<div class="video" style="left:111px">
  <div class="thumb" role="img" aria-label="Two men talking in a library with blue shelves" style="background:linear-gradient(135deg,#2f6f9a,#b98a72 60%,#7f8f76)">
    <svg class="play" width="32" height="32" viewBox="0 0 32 32"><circle cx="16" cy="16" r="15" fill="var(--green-strong)" stroke="#fff" stroke-width="2"/><path d="M13 10l9 6-9 6z" fill="#fff"/></svg>
  </div>
  <p>Lorem Ipsum</p>
</div>
<div class="video" style="left:445px">
  <div class="thumb" role="img" aria-label="Therapist with a tablet seated in a bright office" style="background:linear-gradient(135deg,#e9ecef,#9fb4c8 55%,#d7d2c8)">
    <svg class="play" width="32" height="32" viewBox="0 0 32 32"><circle cx="16" cy="16" r="15" fill="var(--green-strong)" stroke="#fff" stroke-width="2"/><path d="M13 10l9 6-9 6z" fill="#fff"/></svg>
  </div>
  <p>Lorem Ipsum</p>
</div>
<div class="video" style="left:778px">
  <div class="thumb" role="img" aria-label="Counsellor talking with a young man in an office" style="background:linear-gradient(135deg,#c9d4e0,#7b6a5c 55%,#9c5a3a)">
    <svg class="play" width="32" height="32" viewBox="0 0 32 32"><circle cx="16" cy="16" r="15" fill="var(--green-strong)" stroke="#fff" stroke-width="2"/><path d="M13 10l9 6-9 6z" fill="#fff"/></svg>
  </div>
  <p>Lorem Ipsum</p>
</div>
<div class="btn" style="left:518px;top:1238px">VIEW ALL</div>

<!-- conversations -->
<div class="section-title" style="top:1341px">
  <div class="stripes left"><span></span><span></span></div>
  <h2>Truthful Conversations</h2>
  <div class="stripes right"><span></span><span></span></div>
</div>
<p class="intro" style="top:1453px">Lorem ipsum dolor sit amet, consectetur adipiscing elit, sed do eiusmod tempor incididunt ut labore et dolore magna aliqua.<br>Quis ipsum suspendisse ultrices gravida. Risus commodo viverra maecenas accumsan lacus vel facilisis.</p>

<div class="talk" style="left:111px;top:1573px">
  <div class="thumb" role="img" aria-label="Woman recording a podcast with a microphone" style="background:linear-gradient(135deg,#e8ddd0,#c07a3c)"></div>
  <h3>Lorem Ipsum</h3>
  <p>Lorem ipsum dolor sit amet, consectetur adipiscing elit, sed do eiusmod.</p>
  <svg width="18" height="22" viewBox="0 0 18 22"><path d="M0 0l18 11L0 22z" fill="var(--green-strong)"/></svg>
</div>
<div class="talk" style="left:628px;top:1573px">
  <div class="thumb" role="img" aria-label="Podcaster in a studio with purple lighting" style="background:linear-gradient(135deg,#3a2a8a,#8a3fa0 55%,#d0a040)"></div>
  <h3>Lorem Ipsum</h3>
  <p>Lorem ipsum dolor sit amet, consectetur adipiscing elit, sed do eiusmod.</p>
  <svg width="18" height="22" viewBox="0 0 18 22"><path d="M0 0l18 11L0 22z" fill="var(--green-strong)"/></svg>
</div>
<div class="talk" style="left:111px;top:1693px">
  <div class="thumb" role="img" aria-label="Man with headphones speaking into a microphone" style="background:linear-gradient(135deg,#d6d0c4,#7c6a58)"></div>
  <h3>Lorem Ipsum</h3>
  <p>Lorem ipsum dolor sit amet, consectetur adipiscing elit, sed do eiusmod.</p>
  <svg width="18" height="22" viewBox="0 0 18 22"><path d="M0 0l18 11L0 22z" fill="var(--green-strong)"/></svg>
</div>
<div class="talk" style="left:628px;top:1693px">
  <div class="thumb" role="img" aria-label="Man with headphones recording in a dark studio" style="background:linear-gradient(135deg,#2a2e36,#56606c)"></div>
  <h3>Lorem Ipsum</h3>
  <p>Lorem ipsum dolor sit amet, consectetur adipiscing elit, sed do eiusmod.</p>
  <svg width="18" height="22" viewBox="0 0 18 22"><path d="M0 0l18 11L0 22z" fill="var(--green-strong)"/></svg>
</div>
<div class="btn" style="left:518px;top:1853px">VIEW ALL</div>

<!-- about -->
<div class="section-title" style="top:1984px">
  <div class="stripes left"><span></span><span></span></div>
  <h2>About Dr Helen Maddox</h2>
  <div class="stripes right"><span></span><span></span></div>
</div>
<div class="about-frame"></div>
<div class="about-photo" role="img" aria-label="Smiling therapist shaking hands with a client"></div>
<div class="about-copy">
  <p>Lorem ipsum dolor sit amet, consectetur adipiscing elit, sed eiusmod tempor incididunt ut labore et dolore magna aliqua. Quis ipsum suspendisse ultrices gravida. Risus commodo viverra maecenas accumsan lacus vel facilisis.</p>
  <p>Sed ut perspiciatis unde omnis iste natus error sit voluptatem accusantium doloremque laudantium, totam rem aperiam, eaque ipsa quae ab illo inven tore veritatis et quasi architecto beatae vitae dicta sunt explicabo. Nemo enim ipsam voluptatem quia voluptas sit aspernatur aut odit aut fugit, sed quia consequuntur magni dolores eos qui ratione voluptatem.</p>
</div>
<div class="btn" style="left:536px;top:2445px">LEARN MORE</div>

<!-- materials -->
<div class="section-title" style="top:2614px">
  <div class="stripes left"><span></span><span></span></div>
  <h2>Material About Mental Health</h2>
  <div class="stripes right"><span></span><span></span></div>
</div>
<p class="intro" style="top:2724px">Lorem ipsum dolor sit amet, consectetur adipiscing elit, sed do eiusmod tempor incididunt ut labore et dolore magna aliqua.<br>Quis ipsum suspendisse ultrices gravida. Risus commodo viverra maecenas accumsan lacus vel facilisis.</p>

<article class="article" style="left:113px">
  <div class="thumb" role="img" aria-label="Stressed man at a desk holding his glasses" style="background:linear-gradient(135deg,#1e2226,#5a6a7c 55%,#8fb0d0)"></div>
  <h3>Duis aute irure dolor in reprehenderit</h3>
  <div class="date">Aug 21, 2023</div>
  <p>Sed ut perspiciatis unde omnis istelore natus error sitvo luptatem accusantium doloremque laudantium, totam rem aperiam, eaque ipsa quae ab illo inventore.</p>
</article>
<article class="article" style="left:626px">
  <div class="thumb" role="img" aria-label="Smiling woman in a group conversation" style="background:linear-gradient(135deg,#b89a80,#e4ded6 50%,#c49a3c)"></div>
  <h3>Duis aute irure dolor in reprehenderit</h3>
  <div class="date">Aug 21, 2023</div>
  <p>Sed ut perspiciatis unde omnis istelore natus error sitvo luptatem accusantium doloremque laudantium, totam rem aperiam, eaque ipsa quae ab illo inventore.</p>
</article>
<div class="btn" style="left:518px;top:3307px">VIEW ALL</div>

<footer class="site-footer">
  <div class="f-brand display">Dr Helen Maddox</div>
  <p class="f-about">Lorem ipsum dolor sit amet, consectetur adipiscing elit, sed do eiusmod tempor incididunt ut labore et dol magna aliqua. Ut enim ad minim veniam.</p>

  <div class="f-head display" style="left:470px">Visit Us</div>
  <div class="f-item" style="left:470px;top:98px">
    <svg width="14" height="18" viewBox="0 0 14 18"><path d="M7 0a7 7 0 0 0-7 7c0 5 7 11 7 11s7-6 7-11a7 7 0 0 0-7-7z" fill="var(--green-strong)"/><circle cx="7" cy="7" r="2.6" fill="var(--dark)"/></svg>
    Dr Helen Maddox,<br>All Rights Reserved.
  </div>

  <div class="f-head display" style="left:710px">Contact Us</div>
  <div class="f-item" style="left:710px;top:98px">
    <svg width="16" height="16" viewBox="0 0 16 16"><path d="M3.5 0l3 3.5-2 2a10 10 0 0 0 6 6l2-2 3.5 3-2 3.5C7 15 1 9 0 2.5z" fill="var(--green-strong)"/></svg>
    +1 555-010-2244
  </div>
  <div class="f-item" style="left:710px;top:132px">
    <svg width="16" height="12" viewBox="0 0 16 12"><rect width="16" height="12" rx="1" fill="var(--green-strong)"/><path d="M0 1l8 6 8-6" fill="none" stroke="var(--dark)" stroke-width="1.4"/></svg>
    info@drhelenmaddox.com
  </div>

  <div class="f-head display" style="left:988px">Follow Us</div>
  <div class="social" style="top:92px">Brightlane</div>
  <div class="social" style="top:134px">Pagecircle</div>

  <div class="copyright">2023 Dr Helen Maddox. All Rights Reserved.</div>
</footer>

</body>
</html>
```